NEW Wordpress Website Design for a Dynamic Long Term Healthcare Company in Hawaii

I would like a new website design for my current company, Marlow Health Collective, which has two different brands - Marlow Homecare and Marlow Senior Living. You can see the current website at www.marlowhealth-example.com. The website should be built using Wordpress Software and the Framewise theme. The website should have a local Hawaii island/tropical feel, but look professional for healthcare. I'm looking for something fresh, and want the designer to select colors, styles, etc.

In the Header, on all pages, I would like a menu that includes Home Care, Senior Living, Rates, and About Us.
Under each of the Header Menu Titles, I would like these drop downs included:
Home Care (drop down pages)- Nurse Aide Care, 24-Hour Home Care, Skilled Nursing, Lifestyle Aide, Hospice at Home, Bathing & Meal Service.
Senior Living (drop down pages) - Long-Term Stay, Short-Term Stay.
Rates (drop down page) - Rates.
About Us (drop down pages) - Our Mission, Ohana Talk, About Dana Marlow.

In the footer, on all pages, you should include the address: 248 Pueo Lane, Suite 310, Honolulu, HI 96817. Phone number: 808-555-0172
The footer should also include buttons for a page called Learn, Caregiver Jobs, and each of the service page links to include: Nurse Aide Care, 24-Hour Home Care, Skilled Nursing, Lifestyle Aide, Hospice at Home, Bathing & Meal Service.
Please don't take the current website and redesign a few aspects. I'm looking for a completely different look and feel.

Target Market(s)

40-80 year olds

Industry/Entity Type

Long Term Healthcare

Coding

Coded - Design and coding required

Requirements
Should not have
• Our existing website as a template. We are looking for a complete redesign. Thank you.

```html
<!DOCTYPE html>
<html lang="en">
<head>
<meta charset="utf-8">
<title>Marlow Health Collective</title>
<link href="https://fonts.googleapis.com/css2?family=Montserrat:wght@400;500;600;700;800&family=Noto+Sans:wght@400;500&family=Nunito:wght@400;600&display=swap" rel="stylesheet">
<style>
:root{
  --teal:#0f7f7e;
  --teal-text:#2b8fa3;
  --teal-dark:#1d5f80;
  --navy:#254a5a;
  --cream:#f3e3b6;
  --ink:#4a4a4a;
  --footer-bg:#e9e9e2;
  --line:#8cbcc4;
}
*{box-sizing:border-box;margin:0;padding:0}
html,body{width:1200px;height:3011px;overflow:hidden;background:#fff}
body{position:relative;font-family:'Montserrat',sans-serif;color:var(--ink)}
.abs{position:absolute}
.btn{position:absolute;background:var(--teal);color:#fff;display:flex;align-items:center;justify-content:center;font-family:'Noto Sans',sans-serif;letter-spacing:.5px}

/* header */
.brand{position:absolute;top:40px;font-family:'Noto Sans',sans-serif;font-weight:400;color:var(--teal-dark);font-size:15px;line-height:19px}
.brand-left{left:150px;width:90px;text-align:right}
.brand-right{left:258px;width:100px}
.brand-divider{position:absolute;left:248px;top:34px;width:1px;height:60px;background:#999}
.nav a{position:absolute;top:50px;font-family:'Nunito',sans-serif;font-size:18px;color:var(--teal-text);text-decoration:none}
.nav a .caret{font-size:11px;margin-left:8px}

/* hero */
.hero-photo{left:0;top:119px;width:1200px;height:383px;background:linear-gradient(100deg,#a9e6e0 0%,#7fd8d4 18%,#8fdcc0 35%,#9ddb9c 55%,#b2d98a 72%,#86cfa4 88%,#6cc6b0 100%)}
.hero-panel{left:327px;top:272px;width:584px;height:230px;background:rgba(255,255,255,.14)}
.hero-title{left:300px;top:284px;width:638px;text-align:center;color:#fff;font-weight:700;font-size:35px;line-height:40px;letter-spacing:.5px}
.hero-copy{left:330px;top:382px;width:578px;text-align:center;color:#fff;font-size:16.5px;line-height:21px}
.hero-copy u{text-decoration:underline}

/* service cards */
.card{position:absolute;top:598px;width:420px;height:614px;border:1px solid var(--line);background:#fff}
.card-left{left:144px;border-bottom-right-radius:60px}
.card-right{left:637px;border-bottom-left-radius:60px}
.card-art{position:absolute;left:0;top:0;width:100%;height:345px;background:linear-gradient(160deg,#2f7a4e 0%,#14303a 25%,#0b1230 55%,#1a4a3e 85%,#3a7a4a 100%)}
.card-left .card-art{border-top-left-radius:60px;border-bottom-right-radius:70px}
.card-right .card-art{border-top-right-radius:60px;border-bottom-left-radius:70px}
.card-photo{position:absolute;left:43px;top:21px;width:333px;height:242px;border-radius:26px;background:linear-gradient(180deg,#c8a46a 0%,#a8744a 40%,#6e4a36 70%,#8a5e44 100%)}
.card-right .card-photo{background:linear-gradient(180deg,#e6d888 0%,#d4c277 45%,#c9b06e 70%,#ece6c8 100%)}
.card-label{position:absolute;left:0;top:272px;width:100%;text-align:center;color:var(--cream);font-family:'Noto Sans',sans-serif;font-size:40px;letter-spacing:1px}
.card-sub{position:absolute;left:0;top:370px;width:100%;text-align:center;color:var(--teal-text);font-family:'Noto Sans',sans-serif;font-size:24px;font-weight:400}
.card-sub u{text-decoration:underline}
.card-body{position:absolute;left:0;top:418px;width:100%;text-align:center;font-family:'Noto Sans',sans-serif;font-size:14px;line-height:17px;color:#444}
.card-right .card-body{top:408px}
.card .btn{left:8px;top:521px;width:403px;height:53px;font-size:22px}

/* consultation */
.consult-photo{left:144px;top:1258px;width:912px;height:598px;background:linear-gradient(180deg,#5e7e2e 0%,#3c6a2c 25%,#5f8a4c 50%,#9a9c84 78%,#b3a892 100%)}
.consult-title{left:144px;top:1326px;width:912px;text-align:center;color:#fff;font-weight:800;font-size:33px;line-height:41px}
.form-panel{left:210px;top:1422px;width:779px;height:335px;background:#fff}
.field{position:absolute;height:30px;border:1px solid #cfcfcf;border-radius:3px;font-size:14px;color:#444;display:flex;align-items:center;padding-left:17px;background:#fff}
.field.narrow{font-family:'Nunito',sans-serif;font-size:13px;padding-left:13px}
.consent{left:313px;top:1681px;font-size:9.5px;color:#777}
.submit{left:313px;top:1711px;width:574px;height:36px;font-size:21px}

/* testimonials */
.testi-head{left:355px;top:1870px;width:513px;height:111px;border:1px solid var(--line);display:flex;align-items:center;justify-content:center;font-weight:800;font-size:30px;color:#111;letter-spacing:.5px}
.testi{position:absolute;top:1996px;width:274px;height:470px;border:1px solid var(--line);background:#fff}
.testi-icon{position:absolute;left:107px;top:-32px;width:62px;height:62px;border-radius:50%;background:#fff;display:flex;align-items:flex-end;justify-content:center}
.testi-icon span{width:56px;height:56px;border-radius:50%;background:linear-gradient(#f3a27a 0%,#f3a27a 40%,#4ba7c9 60%)}
.testi-text{position:absolute;left:10px;top:72px;width:254px;text-align:center;font-size:13.3px;line-height:19.2px;color:var(--teal-dark);font-weight:500}
.avatar{position:absolute;left:42px;top:320px;width:47px;height:47px;border-radius:50%;background:linear-gradient(#4a3228,#9a6e58 60%,#c4a08a)}
.person{position:absolute;left:102px;top:312px;font-size:13.5px;line-height:19px;color:#222}
.person b{font-weight:600}
.testi .read{position:absolute;left:26px;top:384px;width:225px;height:30px;background:var(--navy);color:#fff;font-size:13px;font-weight:600;display:flex;align-items:center;justify-content:center;border-radius:2px}

/* footer */
.footer{left:0;top:2510px;width:1200px;height:501px;background:radial-gradient(circle at 8% 20%,#8fc1ac 0,transparent 22%),radial-gradient(circle at 95% 92%,#6ea99a 0,transparent 20%),radial-gradient(circle at 60% 100%,#9cc4b3 0,transparent 15%),var(--footer-bg)}
.f-brand{position:absolute;font-family:'Noto Sans',sans-serif;color:var(--teal-dark);font-size:18px;line-height:22px;text-align:center}
.f-btn{left:848px;width:254px;height:52px;font-size:22px}
.social{position:absolute;top:2722px;width:28px;height:28px;border-radius:50%;background:var(--teal-dark)}
.f-head{position:absolute;top:2720px;font-family:'Noto Sans',sans-serif;font-size:25px;color:var(--teal-text);letter-spacing:.5px;font-weight:400}
.f-text{position:absolute;font-family:'Noto Sans',sans-serif;font-size:22px;color:var(--teal-dark);line-height:29px;letter-spacing:.3px}
.f-links{color:var(--teal-text)}
.f-icon{position:absolute;width:38px;height:38px;border-radius:50%;background:#3fcfcf;display:flex;align-items:center;justify-content:center}
.copyright{left:21px;top:2978px;font-size:12px;color:#333}
</style>
</head>
<body>

<header>
  <div class="brand brand-left">Marlow<br>Senior Living</div>
  <div class="brand-divider"></div>
  <div class="brand brand-right" style="top:58px">Marlow<br>Homecare</div>
  <nav class="nav">
    <a style="left:453px">Home Care<span class="caret">&#8964;</span></a>
    <a style="left:600px">Senior Living<span class="caret">&#8964;</span></a>
    <a style="left:756px">Rates<span class="caret">&#8964;</span></a>
    <a style="left:853px">About&nbsp; Us<span class="caret">&#8964;</span></a>
    <a style="left:984px">Contact</a>
  </nav>
</header>

<section class="hero">
  <div class="abs hero-photo" role="img" aria-label="Caregiver and senior sitting together in a bright living room, tinted teal-green"></div>
  <div class="abs hero-panel"></div>
  <h1 class="abs hero-title">HAWAII'S CHOICE<br>HOMECARE &nbsp;&amp;&nbsp; SENIOR LIVING</h1>
  <p class="abs hero-copy"><u>Marlow Homecare</u> provides a variety of professional in-home health care services throughout the entire island of Oahu.<br><br><u>Marlow Senior Living</u>, a beautiful Adult Residential Care Home, is located on the windward side of Oahu in Kailua.</p>
  <div class="btn" style="left:324px;top:502px;width:586px;height:53px;font-family:'Montserrat',sans-serif;font-weight:600;font-size:21px;letter-spacing:1px">OUR SERVICE</div>
</section>

<section>
  <article class="card card-left">
    <div class="card-art" role="img" aria-label="Tropical leaf frame on dark navy">
      <div class="card-photo" role="img" aria-label="Caregiver and resident chatting on a sofa"></div>
      <div class="card-label">SENIOR LIVING</div>
    </div>
    <h2 class="card-sub">Trusted Care In <u>Our</u> Home</h2>
    <p class="card-body">Marlow Senior Living creates a warm, supportive, and enriching care home environment where seniors can thrive in their golden years. We provide residential care that promotes well-being, connection, and dignity of each individual.</p>
    <div class="btn">SCHEDULE TOUR</div>
  </article>
  <article class="card card-right">
    <div class="card-art" role="img" aria-label="Tropical leaf frame on dark navy">
      <div class="card-photo" role="img" aria-label="Caregiver helping a senior man in his bedroom"></div>
      <div class="card-label">HOMECARE</div>
    </div>
    <h2 class="card-sub">Professional Care In <u>Your</u> Home</h2>
    <p class="card-body">Marlow Homecare understands that every person's care journey is unique. We tailor our in-home services to meet the diverse nurturing experience of professional quality care and safety within the comfort and convenience of<br>your own home.</p>
    <div class="btn">SCHEDULE CARE ASSESMENT</div>
  </article>
</section>

<section>
  <div class="abs consult-photo" role="img" aria-label="Senior walking with a walker on a garden path among tropical plants"></div>
  <h2 class="abs consult-title">SCHEDULE A COMPLIMENTARY<br>CARE CONSULTATION</h2>
  <div class="abs form-panel"></div>
  <div class="field" style="left:313px;top:1443px;width:174px">Name*</div>
  <div class="field" style="left:513px;top:1443px;width:174px">Email*</div>
  <div class="field" style="left:713px;top:1443px;width:174px">Phone</div>
  <div class="field narrow" style="left:313px;top:1491px;width:574px">How Can We Help?</div>
  <div class="field" style="left:313px;top:1540px;width:574px"></div>
  <div class="field" style="left:313px;top:1598px;width:574px">How did you hear about us?</div>
  <div class="field narrow" style="left:313px;top:1646px;width:574px">May We Email You About This?</div>
  <div class="abs consent">You agree to receive future emails and understand you may opt-out at any time</div>
  <div class="btn submit">SUBMIT</div>
</section>

<section>
  <div class="abs testi-head">TESTIMONIAL</div>
  <article class="testi" style="left:144px">
    <div class="testi-icon"><span role="img" aria-label="Caregiver team illustration"></span></div>
    <p class="testi-text">The price is really cheap, that's why I bought quite a lot because I wanted to try various variants too.<br>This meatball aci is dry and instant, so we just have to cook it.<br>The price is really cheap, that's why I bought quite a lot because I wanted to try various variants too.<br>This meatball aci is dry and instant, so we just have to cook it.</p>
    <div class="avatar" role="img" aria-label="Reviewer portrait"></div>
    <div class="person"><b>Leilani</b><br>Owner at Kaimana<br>Partners</div>
    <div class="read">Read For Detail</div>
  </article>
  <article class="testi" style="left:458px">
    <div class="testi-icon"><span role="img" aria-label="Caregiver team illustration"></span></div>
    <p class="testi-text">The price is really cheap, that's why I bought quite a lot because I wanted to try various variants too.<br>This meatball aci is dry and instant, so we just have to cook it.<br>The price is really cheap, that's why I bought quite a lot because I wanted to try various variants too.<br>This meatball aci is dry and instant, so we just have to cook it.</p>
    <div class="avatar" role="img" aria-label="Reviewer portrait"></div>
    <div class="person"><b>Leilani</b><br>Owner at Kaimana<br>Partners</div>
    <div class="read">Read For Detail</div>
  </article>
  <article class="testi" style="left:782px">
    <div class="testi-icon"><span role="img" aria-label="Caregiver team illustration"></span></div>
    <p class="testi-text">The price is really cheap, that's why I bought quite a lot because I wanted to try various variants too.<br>This meatball aci is dry and instant, so we just have to cook it.<br>The price is really cheap, that's why I bought quite a lot because I wanted to try various variants too.<br>This meatball aci is dry and instant, so we just have to cook it.</p>
    <div class="avatar" role="img" aria-label="Reviewer portrait"></div>
    <div class="person"><b>Leilani</b><br>Owner at Kaimana<br>Partners</div>
    <div class="read">Read For Detail</div>
  </article>
</section>

<footer>
  <div class="abs footer" role="img" aria-label="Soft tropical leaf background"></div>
  <div class="f-brand" style="left:408px;top:2640px;width:110px">Marlow<br>Homecare</div>
  <div class="f-brand" style="left:520px;top:2590px;width:130px;font-size:20px;line-height:25px">Marlow<br>Health<br>Collective</div>
  <div class="f-brand" style="left:655px;top:2640px;width:125px">Marlow<br>Senior Living</div>

  <div class="btn f-btn" style="top:2539px">LEARN</div>
  <div class="btn f-btn" style="top:2617px">CAREGIVER JOBS</div>

  <div class="social" style="left:848px"></div>
  <div class="social" style="left:896px"></div>
  <div class="social" style="left:944px"></div>
  <div class="social" style="left:992px"></div>

  <h3 class="f-head" style="left:236px">CONTACT US</h3>
  <div class="f-icon" style="left:174px;top:2767px">
    <svg width="22" height="22" viewBox="0 0 24 24" fill="none" stroke="#fff" stroke-width="2"><path d="M5 3h4l2 5-2.5 1.5a11 11 0 0 0 6 6L16 13l5 2v4a2 2 0 0 1-2 2A16 16 0 0 1 3 5a2 2 0 0 1 2-2z"/></svg>
  </div>
  <div class="f-text" style="left:232px;top:2767px">808-555-0172.</div>
  <div class="f-icon" style="left:174px;top:2823px">
    <svg width="20" height="22" viewBox="0 0 24 24" fill="none" stroke="#fff" stroke-width="2"><path d="M12 22s7-7 7-12a7 7 0 0 0-14 0c0 5 7 12 7 12z"/><circle cx="12" cy="10" r="2.5"/></svg>
  </div>
  <div class="f-text" style="left:232px;top:2823px">248 PUEO LANE<br>SUITE 310, HONOLULU<br>HI 96817,</div>

  <h3 class="f-head" style="left:523px">MORE PAGE</h3>
  <div class="f-text f-links" style="left:508px;top:2766px">NURSE AIDE CARE<br>24-HOUR HOME CARE<br>SKILLED NURSING<br>LIFESTYLE AIDE<br>HOSPICE AT HOME<br>BATHING &amp; MEAL SERVICE.</div>

  <div class="abs copyright">© 2023 Marlow Health Collective. All Rights Reserved.</div>
</footer>

</body>
</html>
```